The Brandwell Firm

We need a new design for our letterhead and envelopes. We are a personal injury and criminal defense firm so we need something modern and clean, but more on the professional/traditional side. Our new logo has two colors and is attached to the file so we need something that works well with those colors/matches the design. The following information needs to be on the letterhead:
Phone: (555) 214-3370
Fax: (555) 214-5186
Toll-Free: (888) 431-2059
Post Office Box 4721
Millbrook, SC 29555-4721
HarmClaimCounsel.example
PalmettoTrialAdvocates.example

Target Market(s)

Clients, government agencies, other law firms

Industry/Entity Type

Legal

Font styles to use
Sans Serif
Other font styles liked:
• Arial

Colors

Designer to choose colors to be used in the design.

Requirements
Must have
• Must look professional and clean, modern
Nice to have
• I would like to see a design that works with the logo but does not distract from the content that will be printed on it
Should not have
• Too many colors or crazy designs.

```html
<!DOCTYPE html>
<html lang="en">
<head>
<meta charset="utf-8">
<title>The Brandwell Firm – Letterhead and Envelope</title>
<link rel="stylesheet" href="https://fonts.googleapis.com/css2?family=Arimo:wght@400;700&family=Open+Sans:wght@400;600&display=swap">
<style>
  :root {
    --brand-red: #c81f28;
    --brand-navy: #1f2a8c;
    --ink-gray: #4a4a4a;
    --paper: #ffffff;
    --paper-shade: #f6f6f6;
    --window-gray: #e4e4e4;
    --backdrop: #dcdee2;
  }
  * { box-sizing: border-box; margin: 0; padding: 0; }
  html, body {
    width: 1200px; height: 1200px; overflow: hidden;
    background: var(--backdrop);
  }
  .canvas { position: relative; width: 1200px; height: 1200px; }

  /* ---------- Letterhead ---------- */
  .letterhead {
    position: absolute; left: 70px; top: 50px;
    width: 600px; height: 776px;
    background: linear-gradient(160deg, var(--paper) 60%, var(--paper-shade));
    box-shadow: 0 6px 18px rgba(0,0,0,.18);
    overflow: hidden;
  }
  .contact-block {
    position: absolute; top: 40px; right: 44px;
    font-family: "Arimo", Arial, sans-serif; font-size: 10.5px;
    color: var(--ink-gray); line-height: 1.55;
    list-style: none;
  }
  .contact-block li { display: flex; align-items: flex-start; gap: 6px; }
  .contact-block svg { width: 10px; height: 10px; margin-top: 3px; flex: none; fill: var(--brand-red); }

  .brand-mark {
    display: flex; align-items: center; gap: 10px;
    font-family: "Arimo", Arial, sans-serif; font-weight: 700;
    color: var(--brand-navy); white-space: nowrap;
  }
  .brand-mark .brand-square { background: var(--brand-red); flex: none; }
  .letterhead .brand-mark { position: absolute; left: 48px; top: 150px; font-size: 24px; }
  .letterhead .brand-square { width: 16px; height: 16px; }

  .recipient {
    position: absolute; left: 70px; top: 225px;
    font-family: "Open Sans", Arial, sans-serif; font-size: 10px;
    color: var(--brand-navy); line-height: 1.9;
  }
  .letter-body {
    position: absolute; left: 70px; right: 70px; top: 300px;
    font-family: "Open Sans", Arial, sans-serif; font-size: 10.5px;
    color: var(--brand-navy); line-height: 1.95;
  }
  .letter-body p + p { margin-top: 14px; }
  .closing {
    position: absolute; left: 70px; top: 610px;
    font-family: "Open Sans", Arial, sans-serif; font-size: 10px;
    color: var(--brand-navy);
  }
  .signature {
    margin-top: 8px; width: 130px; height: 38px;
    background: linear-gradient(90deg, rgba(200,31,40,.18), rgba(200,31,40,.05));
    border-radius: 4px;
  }
  .letter-footer { position: absolute; left: 0; bottom: 0; width: 600px; height: 82px; }
  .letter-footer .band { fill: var(--brand-red); }
  .letter-footer .rule { stroke: var(--brand-navy); stroke-width: 3; fill: none; }
  .letter-footer .web {
    font-family: "Arimo", Arial, sans-serif; font-size: 12.5px; fill: #fff;
  }

  /* ---------- Envelope ---------- */
  .envelope {
    position: absolute; left: 470px; top: 870px;
    width: 660px; height: 286px;
    background: linear-gradient(160deg, var(--paper) 55%, var(--paper-shade));
    box-shadow: 0 6px 18px rgba(0,0,0,.2);
    overflow: hidden;
  }
  .envelope .brand-mark { position: absolute; left: 40px; top: 42px; font-size: 22px; }
  .envelope .brand-square { width: 15px; height: 15px; }
  .address-window {
    position: absolute; right: 40px; top: 66px;
    width: 260px; height: 104px; border-radius: 12px;
    background: var(--window-gray);
  }
  .envelope-footer {
    position: absolute; left: 0; bottom: 0; width: 100%; height: 52px;
    background: var(--brand-red);
    display: flex; align-items: center; padding-left: 30px;
    font-family: "Arimo", Arial, sans-serif; font-size: 13.5px; color: #fff;
  }
  .envelope-rule {
    position: absolute; left: 0; bottom: 57px; width: 100%; height: 3px;
    background: var(--brand-navy);
  }
</style>
</head>
<body>
<main class="canvas">

  <section class="letterhead" aria-label="Letterhead">
    <ul class="contact-block">
      <li><svg viewBox="0 0 10 10"><path d="M2 0.5 L4 2.5 L3 4 Q4.5 6 6 7 L7.5 6 L9.5 8 L8 9.5 Q3 9 0.5 2 Z"/></svg>(555) 214-3370</li>
      <li><svg viewBox="0 0 10 10"><rect x="1" y="3" width="8" height="6" rx="1"/><rect x="2.5" y="0.5" width="5" height="3" fill="#fff" stroke="#c81f28" stroke-width="1"/></svg>(555) 214-5186</li>
      <li><svg viewBox="0 0 10 10"><path d="M2 0.5 L4 2.5 L3 4 Q4.5 6 6 7 L7.5 6 L9.5 8 L8 9.5 Q3 9 0.5 2 Z"/></svg>(888) 431-2059</li>
      <li><svg viewBox="0 0 10 10"><path d="M5 0 A3.6 3.6 0 0 1 8.6 3.6 C8.6 6 5 10 5 10 C5 10 1.4 6 1.4 3.6 A3.6 3.6 0 0 1 5 0 Z M5 2.2 A1.4 1.4 0 1 0 5 5 A1.4 1.4 0 1 0 5 2.2 Z"/></svg><span>Post Office Box 4721<br>Millbrook, SC 29555-4721</span></li>
    </ul>

    <div class="brand-mark"><span class="brand-square"></span>The Brandwell Firm</div>

    <div class="recipient">To<br>The,<br>Director</div>

    <div class="letter-body">
      <p>Lorem ipsum dolor sit amet, consectetur adipiscing elit. Sed at ante. Mauris eleifend, quam a vulputate dictum, massa quam dapibus leo, eget vulputate orci purus ut lorem. In fringilla mi in ligula. Pellentesque aliquam quam vel dolor. Nunc adipiscing.</p>
      <p>Vestibulum ut nulla aliquam risus rutrum interdum. Pellentesque augue justo, sagittis et, lacinia at, venenatis non, arcu. Nunc nec orci. Curabitur dolor nunc, egestas at, accumsan at, malesuada nec, primis in faucibus orci luctus et ultrices posuere cubilia curae.</p>
      <p>Integer dignissim viverra velit. Curabitur in odio. Volutpat varius, justo orci elementum dolor, sed imperdiet nulla tellus placerat sit amet, elit.</p>
      <p>Augue justo, sagittis et, lacinia at, venenatis non, arcu. Nunc nec orci. Curabitur dolor nunc, egestas at, accumsan at, malesuada nec. Curabitur in odio.</p>
    </div>

    <div class="closing">
      Thanking you,
      <div class="signature" role="img" aria-label="Handwritten signature"></div>
    </div>

    <svg class="letter-footer" viewBox="0 0 600 82">
      <path class="rule" d="M0 56 H176 L187 24"/>
      <path class="band" d="M0 63 H182 L192 32 Q194 26 202 26 H600 V82 H0 Z"/>
      <text class="web" x="584" y="57" text-anchor="end">HarmClaimCounsel.example | PalmettoTrialAdvocates.example</text>
    </svg>
  </section>

  <section class="envelope" aria-label="Envelope">
    <div class="brand-mark"><span class="brand-square"></span>The Brandwell Firm</div>
    <div class="address-window"></div>
    <div class="envelope-rule"></div>
    <div class="envelope-footer">Post Office Box 4721, Millbrook, SC 29555-4721</div>
  </section>

</main>
</body>
</html>
```